Simple Business Card Design for Tavlo

Job:

Make a very simple, minimalist business card design with my details including adjusted logo. One side to be white (with logo & text). Other side to be yellow - try plain or with logo (or part of logo eg Z). Need business card to have continuity with website.

Logo:
Our logo is made from a free download font website:
http://www.typewell.net/search.php?q=rubber
but the spacing/kerning needs correcting/adjusting as the font spaces unevenly between letters (see attached files). Need logo to be very crisp/sharp when printed.

Printing:
We will be using Plika.com so the design needs to conform to their requirements, see here:

http://uk.plika.com/products/luxe/business-cards.html (scroll down for dimensions and guidelines)

Design:

must say "plant-based food consulting" underneath logo or somewhere
no address needed in contact section
sharp corners (not rounded)
one side white, one side yellow

name: Rosalind Whitcombe
1xmobile number: +44 7700900463
1xtwiiter: @brimcounsel
website address www.orchardtable.com
email address brim@orchardtable.com

Should be easy quick job, prompt + detailed feedback given, am online in UK 9am-10pm for next 3 days. Website is www.orchardtable.com

Industry/Entity Type

Business

Requirements
Must have
• The logo must be corrected. The kerning is not right.

Please use a warm-grey for text

Please submit in matt format, we will be printing matt finish.

Should not have
• Avoid using banners or curvy highlights

Please avoid using black

Please avoid submitting in gloss finish

```html
<!DOCTYPE html>
<html lang="en">
<head>
<meta charset="utf-8">
<title>Brim Business Card</title>
<link rel="stylesheet" href="https://fonts.googleapis.com/css2?family=Cinzel:wght@400;700&display=swap">
<style>
  :root {
    --stage: #6f6f6f;
    --card-white: #ffffff;
    --card-yellow: #f7ec55;
    --accent-icon: #d9c62a;
    --warm-grey: #6b6560;
    --warm-grey-dark: #57514c;
  }
  * { margin: 0; padding: 0; box-sizing: border-box; }
  html, body {
    width: 1200px;
    height: 750px;
    overflow: hidden;
    background: var(--stage);
  }
  .canvas {
    position: relative;
    width: 1200px;
    height: 750px;
    font-family: "Cinzel", serif;
  }
  .card {
    position: absolute;
    top: 210px;
    width: 525px;
    height: 300px;
  }
  .card--front { left: 61px; background: var(--card-white); }
  .card--back  { left: 614px; background: var(--card-yellow); }

  .brand {
    font-family: "Cinzel", serif;
    font-weight: 700;
    color: var(--warm-grey-dark);
    line-height: 1;
    letter-spacing: 0.02em;
  }
  .brand-block {
    position: absolute;
    right: 24px;
    top: 24px;
    text-align: right;
  }
  .brand-block .brand { font-size: 62px; }
  .tagline {
    margin-top: 6px;
    font-size: 10.5px;
    letter-spacing: 0.08em;
    color: var(--warm-grey);
  }
  .card--back .brand {
    position: absolute;
    left: 0;
    right: 0;
    top: 110px;
    text-align: center;
    font-size: 82px;
  }

  .contact-block {
    position: absolute;
    left: 30px;
    top: 168px;
  }
  .person-name {
    font-weight: 700;
    font-size: 15px;
    color: var(--warm-grey-dark);
    line-height: 1.1;
  }
  .person-role {
    font-size: 12px;
    color: var(--warm-grey);
    margin-top: 2px;
  }
  .contact-list {
    list-style: none;
    margin-top: 15px;
  }
  .contact-item {
    display: flex;
    align-items: center;
    height: 15px;
    font-size: 11px;
    color: var(--warm-grey);
  }
  .contact-icon {
    width: 13px;
    height: 11px;
    margin-right: 10px;
    fill: var(--accent-icon);
    flex-shrink: 0;
  }
</style>
</head>
<body>
<div class="canvas">
  <section class="card card--front">
    <div class="brand-block">
      <div class="brand">BRIM</div>
      <div class="tagline">Plant-based food consulting</div>
    </div>
    <div class="contact-block">
      <div class="person-name">Rosalind Whitcombe</div>
      <div class="person-role">Manager</div>
      <ul class="contact-list">
        <li class="contact-item">
          <svg class="contact-icon" viewBox="0 0 13 11" aria-hidden="true">
            <path d="M1 3.5C1 1.5 3 1 6.5 1S12 1.5 12 3.5V4.5H9.5V3.3H3.5V4.5H1Z"/>
            <path d="M3.5 5L4.5 3.8H8.5L9.5 5L11 9.5H2Z"/>
          </svg>
          +44 7700 900463
        </li>
        <li class="contact-item">
          <svg class="contact-icon" viewBox="0 0 13 11" aria-hidden="true">
            <rect x="0.5" y="1" width="12" height="9"/>
            <path d="M1 1.6L6.5 6L12 1.6" fill="none" stroke="#ffffff" stroke-width="1"/>
            <path d="M1 9.6L5 5.5M12 9.6L8 5.5" fill="none" stroke="#ffffff" stroke-width="0.8"/>
          </svg>
          brim@orchardtable.com
        </li>
        <li class="contact-item">
          <svg class="contact-icon" viewBox="0 0 13 11" aria-hidden="true">
            <path d="M1 1H12V8H1Z M2.2 2.2V6.8H10.8V2.2Z" fill-rule="evenodd"/>
            <rect x="4.5" y="8.5" width="4" height="1.5"/>
          </svg>
          www.orchardtable.com
        </li>
        <li class="contact-item">
          <svg class="contact-icon" viewBox="0 0 13 11" aria-hidden="true">
            <circle cx="6.5" cy="5.5" r="4.5"/>
          </svg>
          @brimcounsel
        </li>
      </ul>
    </div>
  </section>

  <section class="card card--back">
    <div class="brand">BRIM</div>
  </section>
</div>
</body>
</html>
```